Business Cards Needed for Innovative Healthcare Marketing Company

We are a marketing company focused on healthcare. Our company is all about rebranding yourself renewing your image and generating results. The phoenix stands for "reborn" or "rising" which we provide new brands for our clients we take their old brands and renew it with creativity and innovation. I am looking for a business card with color dimension. I have attached an example of a card I think has the look and feel of what I am trying to accomplish. I like that the card example has black and grey font colors, I like the font placement and the small logo, I really like the use of the colors on the right those are the colors of my logo. My logo is phoenix so maybe incorporating flames similar to that design. I would like the back a solid color maybe red with an opaque version of the logo and website. As a marketing company I am always open to creative liberty!

Target Market(s)

Doctors and business professionals.

Industry/Entity Type

Marketing

Contact Information for Business Card

Valcorne Health Care Marketing
Marla Tenwick- CEO
#(512)638-2974
email-marla@valcorne.com
website- valcorne.com

Font styles to use
Sans Serif

Colors
ec1f27
f37122
ffc214
fbed22
fbf289
f04a50

Requirements
Must have
• The logo and required information
Nice to have
• icons by the information
Should not have
• child like font

```html
<!DOCTYPE html>
<html lang="en">
<head>
<meta charset="utf-8">
<title>Valcorne Health Care Marketing — Business Card</title>
<link rel="stylesheet" href="https://fonts.googleapis.com/css2?family=Open+Sans:wght@300;400;700&display=swap">
<style>
  :root {
    --page-bg: #e9e4e1;
    --card-white: #ffffff;
    --brand-red: #9c1b22;
    --name-red: #c0282d;
    --flame-orange: #f37122;
    --flame-gold: #f7931e;
    --flame-red: #d8452b;
    --text-grey: #555555;
    --icon-red: #b3262d;
    --back-mark: rgba(255, 255, 255, 0.92);
  }
  * { box-sizing: border-box; margin: 0; padding: 0; }
  html, body {
    width: 1200px;
    height: 950px;
    overflow: hidden;
    background: var(--page-bg);
    font-family: "Open Sans", Arial, sans-serif;
  }
  .sheet {
    width: 1200px;
    height: 950px;
    display: flex;
    flex-direction: column;
    align-items: center;
    justify-content: center;
    gap: 50px;
  }
  .card {
    position: relative;
    width: 700px;
    height: 400px;
    overflow: hidden;
    box-shadow: 0 10px 30px rgba(0, 0, 0, 0.18);
  }

  /* Front */
  .card-front { background: var(--card-white); }
  .phoenix-art {
    position: absolute;
    top: 0;
    right: 0;
    width: 460px;
    height: 190px;
    background: linear-gradient(100deg, rgba(216,69,43,0.25) 0%, var(--flame-red) 35%, var(--flame-orange) 65%, var(--flame-gold) 100%);
    border-bottom-left-radius: 230px 120px;
  }
  .brand-lockup {
    position: absolute;
    left: 44px;
    top: 200px;
    display: flex;
    align-items: center;
    gap: 10px;
  }
  .brand-dot {
    width: 16px;
    height: 16px;
    border-radius: 50%;
    background: var(--flame-orange);
  }
  .brand-name {
    font-weight: 300;
    font-size: 19px;
    letter-spacing: 0.5px;
    color: var(--name-red);
  }
  .holder {
    position: absolute;
    left: 44px;
    top: 248px;
  }
  .holder-name {
    font-weight: 700;
    font-size: 32px;
    color: var(--name-red);
    line-height: 1.1;
  }
  .holder-title {
    font-weight: 400;
    font-size: 19px;
    color: var(--flame-gold);
    margin-top: 2px;
  }
  .contact-list {
    position: absolute;
    left: 44px;
    top: 322px;
    list-style: none;
  }
  .contact-item {
    display: flex;
    align-items: center;
    gap: 10px;
    font-size: 14px;
    color: var(--text-grey);
    line-height: 22px;
  }
  .contact-icon {
    width: 14px;
    height: 14px;
    background: var(--icon-red);
    color: #fff;
    font-size: 9px;
    line-height: 14px;
    text-align: center;
    font-weight: 700;
  }

  /* Back */
  .card-back { background: var(--brand-red); }
  .back-mark {
    position: absolute;
    left: 50%;
    top: 50%;
    transform: translate(-50%, -50%);
    display: flex;
    align-items: center;
    gap: 14px;
  }
  .back-mark-dot {
    width: 26px;
    height: 26px;
    border-radius: 50%;
    background: var(--back-mark);
  }
  .back-mark-name {
    font-weight: 300;
    font-size: 42px;
    letter-spacing: 2px;
    color: var(--back-mark);
  }
  .back-web {
    position: absolute;
    left: 34px;
    top: 50%;
    transform: translateY(-50%) rotate(90deg);
    transform-origin: center;
    font-size: 13px;
    letter-spacing: 4px;
    color: #ffffff;
    font-weight: 300;
  }
</style>
</head>
<body>
  <main class="sheet">
    <section class="card card-front">
      <div class="phoenix-art" role="img" aria-label="Flaming phoenix wing illustration in red, orange and gold"></div>
      <div class="brand-lockup">
        <span class="brand-dot"></span>
        <span class="brand-name">Valcorne Health Care Marketing</span>
      </div>
      <div class="holder">
        <h1 class="holder-name">Marla Tenwick</h1>
        <p class="holder-title">CEO</p>
      </div>
      <ul class="contact-list">
        <li class="contact-item"><span class="contact-icon">p</span>(512)638-2974</li>
        <li class="contact-item"><span class="contact-icon">e</span>marla@valcorne.com</li>
        <li class="contact-item"><span class="contact-icon">w</span>www.valcorne.com</li>
      </ul>
    </section>

    <section class="card card-back">
      <div class="back-mark">
        <span class="back-mark-dot"></span>
        <span class="back-mark-name">Valcorne</span>
      </div>
      <p class="back-web">valcorne.com</p>
    </section>
  </main>
</body>
</html>
```